Wordpress Design Project for Employee Communications Site

We need a Wordpress design for a company that strategizes on and produces materials for employee communications. Improving employee communications at all levels of an organization can help improve overall company performance and results. The site needs to look very clean and professional; we're not afraid of white space. We like the functionality that Wordpress provides; however, we only want one "true" blog page; the other pages should give the impression of a more "static" web site - particularly the home page. I have a logo that I can provide.

I have added these comments to the discussion page:
Great question - thank you for asking it. I’ve done more research

I like the very clean and monochromatic looks to many of these. I don’t have to have monochromatic, but I do like minimal colors. Simple, clean, organized. The home page should “fit” almost entirely without scrolling. I do like fat footers that you can scroll down to. I don’t want a colored background, but any that I’ve chosen with colored backgrounds could be switched to a white background.

http://www.mirabelquennet.example/
http://pondraft.example/
http://v1.samplumworth.example/
http://howdythegoat.example/
http://stayingbrisk.example/
http://www.interiors.kelmun.example/
http://trelvmasters.example/

These last two are more corporate sites. The first one is from a well-respected consultant in my area who does a lot of what I do. And I think Harwenby does a nice job with their site. So, I want to marry the look I like with getting the content job done.

http://www.messagefuelbox.example/
http://www.harwenby.example/view/en_US/us/index.htm

Target Market(s)

Target market is mid- to large-sized companies. More than 500 employees.

Industry/Entity Type

Communications

Requirements
Must have
• Need an impactful home page. There should be a "blog" page; contact us; services; about. For starters, at least. I want fonts to be very readable - that is, either quite dark gray or black.
Nice to have
• I am loathe to include a picture of myself, but I do want some images that say, "professional" and "expert" in communications.
Should not have
• I don't want a hits counter :) (I know no one would do that!).

```html
<!DOCTYPE html>
<html lang="en">
<head>
<meta charset="utf-8">
<title>Halvard Communications Group – Blog</title>
<link rel="stylesheet" href="https://fonts.googleapis.com/css2?family=Ubuntu:ital,wght@0,300;0,400;0,500;1,400;1,500&family=Lora&display=swap">
<style>
:root{
  --ink:#3a3a3a;
  --text:#4a4a4a;
  --muted:#666;
  --blue:#29a9e0;
  --blue-dark:#1a7fb8;
  --olive:#8a9c12;
  --rule:#7a7a7a;
  --foot-bg:#f3f3f3;
  --foot-line:#d8d8d8;
  --fb:#3b5a94;
}
*{box-sizing:border-box;margin:0;padding:0}
html,body{width:959px;height:1200px;overflow:hidden;background:#fff}
body{position:relative;font-family:"Ubuntu",sans-serif;color:var(--text)}
a{color:inherit;text-decoration:none}

.brand{position:absolute;left:65px;top:30px;display:flex;align-items:center;gap:10px}
.brand-dot{width:34px;height:34px;border-radius:50%;background:var(--blue)}
.brand-name{font-weight:400;font-size:21px;color:#9cc21a;letter-spacing:.2px}

.nav-rule{position:absolute;top:102px;height:2px;background:var(--rule)}
.main-nav{position:absolute;left:530px;top:92px;display:flex;align-items:center;font-size:15px;font-weight:300;color:var(--ink);background:#fff;padding:0 4px}
.main-nav a{padding:0 13px;position:relative;line-height:18px}
.main-nav a+a{border-left:1px solid #555}
.main-nav .current{color:var(--blue)}
.main-nav .current svg{position:absolute;left:50%;top:20px;margin-left:-4px}

.hero{position:absolute;left:72px;top:123px;width:785px;height:210px;background:linear-gradient(180deg,#aac2dc 0%,#d6e2ee 55%,#c9a98e 100%)}
.hero-note{position:absolute;left:22px;top:32px;width:385px;height:139px;background:rgba(255,255,255,.82);border:2px solid rgba(255,255,255,.95);box-shadow:0 0 3px rgba(0,0,0,.12);padding:10px 16px;font-size:21.5px;line-height:28px;color:var(--ink);font-weight:300}
.hero-note strong{color:var(--blue-dark);font-weight:500}

.post{position:absolute;left:0;width:959px;height:320px}
.date-ribbon{position:absolute;left:55px;top:0;width:82px;height:78px}
.date-ribbon .date{position:absolute;left:13px;top:8px;width:57px;text-align:center;font-family:"Lora",serif;color:#fff;font-size:16px;line-height:16px}
.post-title{position:absolute;left:148px;top:6px;font-size:18px;font-weight:300;color:#444}
.post-meta{position:absolute;left:155px;top:46px;font-size:10px;display:flex;align-items:center;color:var(--muted)}
.post-meta .author{color:var(--olive)}
.post-meta .sep{margin:0 16px}
.post-meta svg{margin-left:7px}
.post-photo{position:absolute;left:65px;top:100px;width:229px;height:171px;background:#f3f3f3;padding:5px}
.post-photo .fill{width:219px;height:145px;background:linear-gradient(135deg,#2b4f86 0%,#4d73a8 45%,#1e2f4c 100%);box-shadow:0 8px 7px -4px rgba(0,0,0,.45)}
.post-body{position:absolute;left:313px;top:112px;width:585px;font-size:9.4px;line-height:15.7px;color:var(--text)}
.post-body .lead{font-style:italic;font-weight:500;color:#444}
.post-body p+p{margin-top:14px}
.read-more{position:absolute;left:315px;top:288px;font-size:10px;font-style:italic;color:var(--blue);text-decoration:underline}
.share{position:absolute;top:278px;height:20px;font-size:9px;display:flex;align-items:center;justify-content:center;border-radius:2px}
.share-fb{left:776px;width:59px;background:var(--fb);color:#fff;letter-spacing:.4px}
.share-post{left:842px;width:57px;background:#f6fbfe;border:1px solid #c9dfe9;color:var(--blue-dark);font-size:12px}
.post-divider{position:absolute;left:88px;top:313px;width:810px;border-top:2px dotted #ddd}

.site-footer{position:absolute;left:0;top:1018px;width:959px;height:152px;background:var(--foot-bg);border-top:1px solid var(--foot-line)}
.foot-col{position:absolute;top:14px;height:123px;font-size:9.2px;letter-spacing:.4px;color:#444}
.foot-col+.foot-col{border-left:1px solid #d2d2d2}
.foot-col h4{font-size:11.5px;font-weight:500;color:#333;margin:8px 0 10px;letter-spacing:.2px}
.foot-col li{list-style:none;line-height:15.7px}
.social{display:flex;gap:6px}
.social span{width:14px;height:14px;border-radius:2px;background:#3d8fcb}
.copyright{position:absolute;left:0;top:1170px;width:959px;height:28px;border-top:1px solid #ddd;text-align:center;font-size:9.4px;line-height:28px;color:#333;letter-spacing:.2px}
.bottom-rule{position:absolute;left:0;top:1197px;width:959px;height:3px;background:#333}
</style>
</head>
<body>

<header class="site-header">
  <a class="brand" href="#"><span class="brand-dot"></span><span class="brand-name">Halvard Communications Group</span></a>
  <div class="nav-rule" style="left:0;width:530px"></div>
  <div class="nav-rule" style="left:835px;width:124px"></div>
  <nav class="main-nav">
    <a class="current" href="#">works<svg width="8" height="5" viewBox="0 0 8 5"><path d="M1 1l3 3 3-3" fill="none" stroke="#29a9e0" stroke-width="1.3"/></svg></a>
    <a href="#">process</a>
    <a href="#">about</a>
    <a href="#">contact</a>
  </nav>
</header>

<section class="hero" role="img" aria-label="Photo of hands forming a star shape against a bright sky">
  <div class="hero-note">Now more than ever it is critical to show the value of <strong>Employee Communication</strong> and Engagement to the business.</div>
</section>

<article class="post" style="top:355px">
  <svg class="date-ribbon" viewBox="0 0 82 78"><rect x="0" y="0" width="82" height="3" fill="#d9d9d9"/><path d="M13 3h57v72L41.5 50 13 75z" fill="#29a9e0"/></svg>
  <div class="date-ribbon"><div class="date">AUG<br>10</div></div>
  <h2 class="post-title">Organizational and Business Communications</h2>
  <div class="post-meta"><span class="author">Posted by Marlowek</span><span class="sep">|</span><span>2 Comments</span><svg width="15" height="13" viewBox="0 0 15 13"><path d="M2 1h11a1 1 0 011 1v6a1 1 0 01-1 1H7l-3 3V9H2a1 1 0 01-1-1V2a1 1 0 011-1z" fill="none" stroke="#888"/><path d="M4 4h7M4 6h5" stroke="#aaa"/></svg></div>
  <figure class="post-photo"><div class="fill" role="img" aria-label="Photo of a presenter in a suit speaking on stage"></div></figure>
  <div class="post-body">
    <p><span class="lead">Here is a brief exercise that I used in teaching nonverbal communication and that I rewrote for a textbook in nonverbal that I’m in the process of writing. Here I use it as an introduction to the discussion</span> of height but it can also be used with perception, stereotypes, and media influences, for example. You can adjust it in any way you’d like for your own classes.</p>
    <p>Workplace Messaging Bulletin: Find out what’s going on in the world of corporate and business communications.<br>Petra Lindholm: This consultant and expert offers insight into business and organizational communications.<br>Message Undertones: Learn about using communications to better communicate within your organization, and with others outside your organization.<br>Clearer Outcomes Daily: This Aussie knows how to communicate more effectively in business settings.<br>Boardroom Lens: This blog is meant for corporate communications professionals.</p>
  </div>
  <a class="read-more" href="#">Contineue Reading</a>
  <a class="share share-fb" href="#">SHARE</a>
  <a class="share share-post" href="#">Post</a>
  <div class="post-divider"></div>
</article>

<article class="post" style="top:692px">
  <svg class="date-ribbon" viewBox="0 0 82 78"><rect x="0" y="0" width="82" height="3" fill="#d9d9d9"/><path d="M13 3h57v72L41.5 50 13 75z" fill="#29a9e0"/></svg>
  <div class="date-ribbon"><div class="date">AUG<br>10</div></div>
  <h2 class="post-title">Organizational and Business Communications</h2>
  <div class="post-meta"><span class="author">Posted by Marlowek</span><span class="sep">|</span><span>2 Comments</span><svg width="15" height="13" viewBox="0 0 15 13"><path d="M2 1h11a1 1 0 011 1v6a1 1 0 01-1 1H7l-3 3V9H2a1 1 0 01-1-1V2a1 1 0 011-1z" fill="none" stroke="#888"/><path d="M4 4h7M4 6h5" stroke="#aaa"/></svg></div>
  <figure class="post-photo"><div class="fill" role="img" aria-label="Photo of a presenter in a suit speaking on stage"></div></figure>
  <div class="post-body">
    <p><span class="lead">Here is a brief exercise that I used in teaching nonverbal communication and that I rewrote for a textbook in nonverbal that I’m in the process of writing. Here I use it as an introduction to the discussion</span> of height but it can also be used with perception, stereotypes, and media influences, for example. You can adjust it in any way you’d like for your own classes.</p>
    <p>Workplace Messaging Bulletin: Find out what’s going on in the world of corporate and business communications.<br>Petra Lindholm: This consultant and expert offers insight into business and organizational communications.<br>Message Undertones: Learn about using communications to better communicate within your organization, and with others outside your organization.<br>Clearer Outcomes Daily: This Aussie knows how to communicate more effectively in business settings.<br>Boardroom Lens: This blog is meant for corporate communications professionals.</p>
  </div>
  <a class="read-more" href="#">Contineue Reading</a>
  <a class="share share-fb" href="#">SHARE</a>
  <a class="share share-post" href="#">Post</a>
  <div class="post-divider"></div>
</article>

<footer class="site-footer">
  <div class="foot-col" style="left:124px;width:104px"><h4>Company</h4><ul><li>About Us</li><li>Sitemap</li><li>Website Terms</li><li>Terms of Business</li><li>Privacy Policy</li></ul></div>
  <div class="foot-col" style="left:228px;width:149px;padding-left:28px"><h4>Product</h4><ul><li>Business Websites</li><li>Reviews</li><li>Quick Tour</li><li>Pricing</li><li>Free Trial</li></ul></div>
  <div class="foot-col" style="left:377px;width:178px;padding-left:33px"><h4>Internet Marketing</h4><ul><li>Marketing Tips</li><li>Search Optimisation</li><li>Social Media</li><li>Video Marketing</li><li>Business Cases</li></ul></div>
  <div class="foot-col" style="left:555px;width:155px;padding-left:34px"><h4>Services</h4><ul><li>Help/Contact us</li><li>Business directory</li><li>Legal notices</li><li>Privacy policy</li><li>Terms &amp; Conditions</li></ul></div>
  <div class="foot-col" style="left:710px;width:120px;padding-left:27px"><h4>Follow us</h4><div class="social"><span></span><span></span><span></span><span></span></div></div>
</footer>
<div class="copyright">Copyright © 2012 Halvard Communications Group. All rights reserved.</div>
<div class="bottom-rule"></div>

</body>
</html>
```